Climbing Gear Company Stationary Design

We need some new stationary to standardise our business.
We require:

Business Card
A4 Letterhead
With complements slip

Our business is a Distributor and retailer of rock climbing equipment throughout Australia.
We need to the stationary (business card in particular) to reflect this.

Target Market(s)

customers, other retail outlets, overseas manufacturers.

Industry/Entity Type

Business

Requirements
Must have
• company logo
website url- www.ridgetopgearworks.com.au
email - mark@ridgetopgearworks.com
Business Address: Unit 3, 14-16 Marlowe Street, Tallowvale, VIC, 2371
Phone: 0438 627 194
my Name (on Business card) - Gordon Pellimore
use of Blue colour in our logo

```html
<!DOCTYPE html>
<html lang="en">
<head>
<meta charset="utf-8">
<title>Ridgetop Gearworks — Business Card</title>
<link rel="stylesheet" href="https://fonts.googleapis.com/css2?family=Source+Sans+3:wght@400;600;700&display=swap">
<style>
  :root {
    --brand-blue: #1f4189;
    --swoosh-grey: #d9dbe0;
    --card-white: #ffffff;
    --faded-blue: #bcc6dc;
    --backdrop: #ecebe8;
    --web-blue: #2a4a8f;
  }
  * { margin: 0; padding: 0; box-sizing: border-box; }
  html, body {
    width: 1200px; height: 483px; overflow: hidden;
    background: var(--backdrop);
    font-family: "Source Sans 3", sans-serif;
  }
  .card {
    position: absolute; top: 90px;
    width: 525px; height: 300px;
    border-radius: 16px; overflow: hidden;
    background: var(--card-white);
  }
  .card--front { left: 53px; }
  .card--back { left: 613px; }
  .card__shapes { position: absolute; inset: 0; }

  .brand-name {
    position: absolute;
    font-weight: 700; text-transform: uppercase; white-space: nowrap;
    color: var(--brand-blue);
  }
  .tagline {
    position: absolute; white-space: nowrap;
    font-weight: 400; color: var(--brand-blue); text-transform: uppercase;
  }
  .card--front .brand-name { left: 47px; top: 50px; font-size: 28px; letter-spacing: 1.5px; }
  .card--front .tagline { left: 48px; top: 88px; font-size: 12.5px; letter-spacing: 2.6px; }

  .holder-name {
    position: absolute; left: 50px; top: 221px;
    color: var(--card-white); font-weight: 700; font-size: 14.5px; letter-spacing: .3px;
  }
  .divider {
    position: absolute; left: 268px; top: 180px; width: 1px; height: 94px;
    background: rgba(255,255,255,.55);
  }
  .contact {
    position: absolute; left: 288px; top: 177px;
    color: var(--card-white); font-size: 11.5px; line-height: 19px; list-style: none;
  }
  .contact__gap { margin-top: 5px; }

  .card--back .brand-name {
    left: 0; right: 0; top: 106px; text-align: center;
    font-size: 40px; letter-spacing: 2px; color: var(--faded-blue);
  }
  .card--back .tagline {
    left: 0; right: 0; top: 166px; text-align: center;
    font-size: 16.5px; letter-spacing: 4.4px; color: var(--faded-blue);
  }
  .card--back .website {
    position: absolute; left: 0; right: 0; top: 205px; text-align: center;
    font-size: 13px; letter-spacing: 2.2px; color: var(--web-blue);
  }
</style>
</head>
<body>
  <section class="card card--front">
    <svg class="card__shapes" width="525" height="300" viewBox="0 0 525 300" aria-hidden="true">
      <path d="M0,138 C170,178 400,120 480,0 L493,0 C430,115 250,170 0,148 Z" fill="var(--swoosh-grey)"/>
      <path d="M0,140 C190,185 420,130 492,0 L525,0 L525,300 L0,300 Z" fill="var(--brand-blue)"/>
    </svg>
    <div class="brand-name">Ridgetop Gearworks</div>
    <div class="tagline">Equipping Australian Climbers</div>
    <div class="holder-name">GORDON PELLIMORE</div>
    <div class="divider"></div>
    <ul class="contact">
      <li>Unit 3, 14-16 Marlowe Street</li>
      <li>Tallowvale, VIC, 2371</li>
      <li class="contact__gap">P : 0438 627 194</li>
      <li>E : mark@ridgetopgearworks.com</li>
      <li>W: www.ridgetopgearworks.com.au</li>
    </ul>
  </section>

  <section class="card card--back">
    <div class="brand-name">Ridgetop Gearworks</div>
    <div class="tagline">Equipping Australian Climbers</div>
    <div class="website">www.ridgetopgearworks.com.au</div>
  </section>
</body>
</html>
```